Exciting opportunity to create logo and a label for our natural health brand.

About us

We are a customer centric health supplement brand who believes in natural medicine and high quality ingredients. We take a holistic approach to healthcare, with an eastern philosophy. We believe in being partners with our customers in their health care journey and are invested in their well being.

Our brand philosophy and values are attached (see Vorna philosophy.png). Our personality traits are:

- Natural
- Fresh
- Modern
- Balanced (in a holistic sense)

Task breakdown

1. Design a fresh feeling logo for us
- We want it to represent our values and high quality ingredients. We would like the quality of the product to be reflected in the branding and have a high end feel.
- Logo text must include Vorna Health Sciences
- We want the Vorna to be the focus of the logo (see uploaded image Vorna logo example.png)
The logo does not have to follow this layout, but we just want the Vorna to stand out. Feel free to use your creative license on this!

2. Create an attractive label to go on the supplement bottle
- The designs need to be eye catching, give a sense of high end ingredients and natural products and tie in with the logo to give a joined up feel.
- We are selling our products online and need them to really stand out from the competition.
- See examples of labels and packaging we like (1 -7 label design).

The initial label we would like you to design would be for our product Calm Drift. It is a product that assists in the management of Anxiety and stress. The label will appear on the bottle that holds the capsules for this supplement, see uploaded files (Example plain bottles.png). The bottles may be white as the picture shows or dark blue recyclable plastic or dark brown glass . We don't have the exact dimensions of the bottle yet, but I will follow up with these.

The label needs to include the following things:
1. The logo
2. The name of the product
3. The product is to help with the relief of Anxiety and Stress
4. Number of capsules the bottle contains
5. The back of the label should have
i) The ingredients
ii) Dosage
iii) Directions of use

Please use placeholder text where needed.

We look forward to seeing your design. Thank you.

```html
<!DOCTYPE html>
<html lang="en">
<head>
<meta charset="utf-8">
<title>Vorna Health Sciences — Calm Drift label</title>
<link rel="stylesheet" href="https://fonts.googleapis.com/css2?family=Playfair+Display:wght@400&family=Libre+Baskerville:wght@700&family=Barlow:wght@500;600;700&display=swap">
<style>
  :root {
    --backdrop: #6e8b4d;
    --label-white: #ffffff;
    --gold-light: #f2c063;
    --gold-bright: #fcd27d;
    --gold-mid: #b89248;
    --gold-deep: #ac8a4f;
    --ink: #232323;
    --sage-dark: #5b763b;
    --sage-light: #8daf74;
    --text-light: #ffffff;
  }
  * { margin: 0; padding: 0; box-sizing: border-box; }
  html, body {
    width: 1200px;
    height: 750px;
    overflow: hidden;
    background: var(--backdrop);
  }
  .canvas {
    position: relative;
    width: 1200px;
    height: 750px;
    background: var(--backdrop);
  }
  .label {
    position: absolute;
    left: 430px;
    top: 232px;
    width: 340px;
    height: 420px;
    background: var(--label-white);
  }
  .gold-band {
    position: absolute;
    left: 29px;
    right: 22px;
    background: linear-gradient(90deg, var(--gold-light) 0%, var(--gold-bright) 30%, var(--gold-mid) 62%, var(--gold-deep) 100%);
  }
  .gold-band--top { top: 0; height: 128px; }
  .gold-band--bottom { top: 304px; height: 108px; }
  .brand {
    position: absolute;
    left: 0; right: 0;
    text-align: center;
    color: var(--text-light);
    font-family: "Playfair Display", serif;
    font-weight: 400;
  }
  .brand__name {
    top: 22px;
    font-size: 66px;
    line-height: 1;
    letter-spacing: 0.01em;
  }
  .brand__descriptor {
    top: 104px;
    font-size: 8px;
    letter-spacing: 0.62em;
    padding-left: 0.62em;
  }
  .product-name {
    position: absolute;
    top: 136px;
    left: 0; right: 0;
    text-align: center;
    font-family: "Libre Baskerville", serif;
    font-weight: 700;
    font-size: 25px;
    letter-spacing: 0.12em;
    color: var(--ink);
  }
  .benefit-strip {
    position: absolute;
    top: 161px;
    left: 29px;
    right: 22px;
    height: 15px;
    background: linear-gradient(90deg, var(--sage-dark) 0%, var(--sage-light) 100%);
    color: var(--text-light);
    font-family: "Barlow", sans-serif;
    font-weight: 600;
    font-size: 8.5px;
    letter-spacing: 0.18em;
    line-height: 15px;
    text-align: center;
  }
  .botanical {
    position: absolute;
    top: 186px;
    left: 98px;
    width: 158px;
    height: 120px;
  }
  .capsule-count {
    position: absolute;
    top: 340px;
    left: 29px;
    right: 22px;
    text-align: center;
    color: var(--text-light);
    font-family: "Barlow", sans-serif;
  }
  .capsule-count__number {
    display: block;
    font-weight: 700;
    font-size: 21px;
    line-height: 1;
  }
  .capsule-count__unit {
    display: block;
    font-weight: 600;
    font-size: 15px;
    letter-spacing: 0.08em;
    line-height: 1.2;
  }
</style>
</head>
<body>
  <main class="canvas">
    <section class="label">
      <div class="gold-band gold-band--top">
        <p class="brand brand__name">Vorna</p>
        <p class="brand brand__descriptor">HEALTH SCIENCES</p>
      </div>

      <h1 class="product-name">CALM DRIFT</h1>
      <p class="benefit-strip">REDUCE STRESS AND ANXIETY NATURALLY</p>

      <svg class="botanical" viewBox="0 0 158 120" role="img" aria-label="Gold illustration of blossoming flowers on leafy stems">
        <defs>
          <radialGradient id="blossom-tone" cx="50%" cy="50%" r="55%">
            <stop offset="0%" stop-color="#f4c66a"/>
            <stop offset="70%" stop-color="#dcae58" stop-opacity="0.75"/>
            <stop offset="100%" stop-color="#dcae58" stop-opacity="0"/>
          </radialGradient>
        </defs>
        <rect x="0" y="0" width="158" height="120" fill="url(#blossom-tone)"/>
      </svg>

      <div class="gold-band gold-band--bottom"></div>
      <p class="capsule-count">
        <span class="capsule-count__number">60</span>
        <span class="capsule-count__unit">capsules</span>
      </p>
    </section>
  </main>
</body>
</html>
```